Business card for Eyelash extension salon in Beverly Hills,California USA

We need new business card for our salon in Beverly Hills. The salon name is 'Lashvera' . We would like to have...Business name: Lashvera Name of person: will provide later Address 4720 N.Alder Crest Ave Beverly Hills , CA 90210 Phone: will provide later (Text only) Web: www.lashverastudio.example Snapgrid icon, Circlebook icon follow us for seasonal campaign and news @lashverastudiolounge Design should look elegant, high-end, clean, simple, cohesive with my brand. Please refer my brand board. Business name color will be metallic bronzy color. Im thinking grey background or white background. Thanks

Target Market(s)

25-35. Gender neutral. People who are in Entertainment business industry.
This is High-end Eyelash extension salon in Beverly Hills

Industry/Entity Type

Beauty Salon

Contact Information for Business Card

Business name: Lashvera
Name of person: will provide later
Address 4720 N.Alder Crest Ave Beverly Hills , CA 90210
Phone: will provide later (Text only)
Web: www.lashverastudio.example
Snapgrid icon, Circlebook icon
follow us for seasonal campaign and news @lashverastudiolounge

Requirements
Must have
• Beautiful, elegant, clean and simple look but very attractive and modern
Should not have
• We don't like too clutter, too busy designs.

```html
<!DOCTYPE html>
<html lang="en">
<head>
<meta charset="utf-8">
<title>Lashvera Beverly Hills – Business Card</title>
<link rel="stylesheet" href="https://fonts.googleapis.com/css2?family=Playfair+Display:wght@700&family=Poppins:wght@300;400;500;600&display=swap">
<style>
  :root {
    --canvas-bg: #2b2c30;
    --card-black: #0c0c0d;
    --marble-light: #f4f5f6;
    --marble-mid: #dfe1e4;
    --ink: #141414;
    --bronze: #b9856a;
    --bronze-soft: #a8775d;
  }
  * { margin: 0; padding: 0; box-sizing: border-box; }
  html, body {
    width: 1200px; height: 900px; overflow: hidden;
    background: var(--canvas-bg);
  }
  .canvas {
    position: relative; width: 1200px; height: 900px;
    display: flex; align-items: center; justify-content: center; gap: 50px;
  }
  .card {
    position: relative; width: 520px; height: 298px;
    border-radius: 4px; overflow: hidden;
    box-shadow: 0 12px 30px rgba(0,0,0,0.45);
  }

  /* Back side */
  .card-back { color: var(--ink); font-family: "Poppins", sans-serif; }
  .marble-surface {
    position: absolute; inset: 0;
    background:
      radial-gradient(ellipse at 25% 30%, var(--marble-mid) 0%, transparent 45%),
      radial-gradient(ellipse at 80% 75%, var(--marble-mid) 0%, transparent 40%),
      var(--marble-light);
  }
  .back-content {
    position: relative; height: 100%;
    display: flex; flex-direction: column; align-items: center;
    padding-top: 40px;
  }
  .person-name {
    font-family: "Playfair Display", serif; font-weight: 700;
    font-size: 22px; letter-spacing: 0.5px; text-transform: uppercase;
  }
  .contact-row {
    display: flex; align-items: center; margin-top: 22px;
  }
  .contact-left, .contact-right {
    width: 210px; font-size: 13px; line-height: 1.45; font-weight: 400;
  }
  .contact-left { text-align: right; }
  .contact-divider {
    width: 1.5px; height: 64px; background: var(--ink); margin: 0 18px;
  }
  .follow-line {
    margin-top: 24px; font-size: 13px; font-weight: 600;
  }
  .social-row {
    display: flex; align-items: center; gap: 8px; margin-top: 12px;
    font-size: 13px; font-weight: 500;
  }
  .social-dot {
    width: 20px; height: 20px; border-radius: 50%; background: var(--ink);
  }
  .social-name { font-size: 11px; font-weight: 500; }
  .social-handle { margin: 0 8px; }

  /* Front side */
  .card-front {
    background: linear-gradient(135deg, #1a1a1c 0%, var(--card-black) 55%);
    display: flex; flex-direction: column; align-items: center; justify-content: center;
  }
  .brand-name {
    font-family: "Poppins", sans-serif; font-weight: 300;
    font-size: 78px; color: var(--bronze); letter-spacing: 1px; line-height: 1;
  }
  .brand-location {
    margin-top: 16px; font-family: "Poppins", sans-serif; font-weight: 400;
    font-size: 12px; letter-spacing: 4px; text-transform: uppercase;
    color: var(--bronze-soft);
  }
</style>
</head>
<body>
<main class="canvas">
  <section class="card card-back">
    <div class="marble-surface" role="img" aria-label="White marble texture with soft grey veining"></div>
    <div class="back-content">
      <h1 class="person-name">Johnathan Doe</h1>
      <div class="contact-row">
        <div class="contact-left">
          <p>123 456 7890 (Text only)</p>
          <p>www.lashverastudio.example</p>
        </div>
        <div class="contact-divider"></div>
        <div class="contact-right">
          <p>4720 N.Alder Crest Ave,</p>
          <p>Beverly Hills , CA 90210</p>
        </div>
      </div>
      <p class="follow-line">Follow us for seasonal campaign and news</p>
      <div class="social-row">
        <span class="social-dot"></span><span class="social-name">Circlebook</span>
        <span class="social-handle">@lashverastudiolounge</span>
        <span class="social-dot"></span><span class="social-name">Snapgrid</span>
      </div>
    </div>
  </section>

  <section class="card card-front">
    <h2 class="brand-name">Lashvera</h2>
    <p class="brand-location">Beverly Hills</p>
  </section>
</main>
</body>
</html>
```